Hollow Thicket, a 3d voxel survival video game needs a card for gaming conventions

I am the lead developer for Hollow Thicket http://www.HollowThicket.example and need a business card to hand out at an indie gaming convention
The card would need to include the game name, website url, my name, position (Lead Developer), e-mail and phone number
The game is a 3d, voxel (with smooth terrain) based survival game with guns and wildlife. The main icon of the game would likely be a grizzly bear but I am willing to accept other designs too.
Attached is a media kit for the game with some images you can use but don't have to its just what little art I can provide. Anything on the website or from the video game can also be used. unrelated art can also be used.
Target Market(s)
Indie Developers/publishers at conferences
Industry/Entity Type
Games
Contact Information for Business Card
Name: Corin Waldrick
Position: Lead Developer
E-mail: Pale_Kettle@mailbox.example
Phone number: 555-372-1186

```html
<!DOCTYPE html>
<html lang="en">
<head>
<meta charset="utf-8">
<title>Hollow Thicket — Business Card</title>
<link href="https://fonts.googleapis.com/css2?family=Open+Sans:wght@400;600;800&display=swap" rel="stylesheet">
<style>
  :root {
    --page-bg: #ecebe8;
    --card-bg: #1f2a33;
    --accent-orange: #e2683c;
    --text-light: #f4f4f2;
    --logo-tone: #e2683c;
    --bear-dark: #3b2a1e;
    --bear-mid: #7a5233;
    --bear-light: #b07a45;
  }
  * { margin: 0; padding: 0; box-sizing: border-box; }
  html, body {
    width: 1200px; height: 900px; overflow: hidden;
    background: var(--page-bg);
    font-family: "Open Sans", Arial, sans-serif;
  }
  .canvas { position: relative; width: 1200px; height: 900px; }
  .card {
    position: absolute;
    background: var(--card-bg);
    box-shadow: 0 6px 18px rgba(0,0,0,0.22);
    overflow: hidden;
  }
  .card--front { left: 238px; top: 62px; width: 556px; height: 343px; }
  .card--back  { left: 457px; top: 518px; width: 560px; height: 343px; }

  .game-name {
    position: absolute;
    color: var(--logo-tone);
    font-weight: 800;
    text-transform: uppercase;
    line-height: 1.02;
    letter-spacing: 1px;
  }
  .card--front .game-name { left: 36px; top: 34px; font-size: 40px; }
  .card--back .game-name {
    left: 0; right: 0; top: 120px;
    text-align: center; font-size: 42px;
  }

  .contact-person { position: absolute; left: 37px; top: 188px; }
  .person-name { color: var(--accent-orange); font-size: 17px; font-weight: 600; line-height: 1.2; }
  .person-role { color: var(--text-light); font-size: 15px; line-height: 1.3; }

  .contact-list { position: absolute; left: 37px; top: 259px; list-style: none; }
  .contact-item {
    display: flex; align-items: center; gap: 8px;
    color: var(--text-light); font-size: 15px; line-height: 20px;
  }
  .contact-icon { width: 12px; height: 12px; flex: none; }

  .mascot-area {
    position: absolute; right: 0; bottom: 0;
    width: 196px; height: 224px;
    border-radius: 60px 0 0 0;
    background: radial-gradient(ellipse at 55% 45%, var(--bear-light) 0%, var(--bear-mid) 45%, var(--bear-dark) 100%);
  }
</style>
</head>
<body>
<main class="canvas">
  <section class="card card--front">
    <div class="game-name">Hollow<br>Thicket</div>
    <div class="contact-person">
      <p class="person-name">Corin Waldrick</p>
      <p class="person-role">Lead Developer</p>
    </div>
    <ul class="contact-list">
      <li class="contact-item">
        <svg class="contact-icon" viewBox="0 0 24 24" aria-hidden="true"><path fill="#e2683c" d="M6.6 10.8a15.1 15.1 0 0 0 6.6 6.6l2.2-2.2c.3-.3.7-.4 1-.2 1.1.4 2.3.6 3.6.6.6 0 1 .4 1 1V20c0 .6-.4 1-1 1A17 17 0 0 1 3 4c0-.6.4-1 1-1h3.5c.6 0 1 .4 1 1 0 1.3.2 2.5.6 3.6.1.3 0 .7-.2 1z"/></svg>
        555-372-1186
      </li>
      <li class="contact-item">
        <svg class="contact-icon" viewBox="0 0 24 24" aria-hidden="true"><rect x="2" y="5" width="20" height="14" rx="1" fill="#e2683c"/><path d="M2 6l10 7 10-7" fill="none" stroke="#1f2a33" stroke-width="1.6"/></svg>
        Pale_Kettle@mailbox.example
      </li>
      <li class="contact-item">
        <svg class="contact-icon" viewBox="0 0 24 24" aria-hidden="true"><circle cx="12" cy="12" r="10" fill="none" stroke="#e2683c" stroke-width="2.4"/><ellipse cx="12" cy="12" rx="4.5" ry="10" fill="none" stroke="#e2683c" stroke-width="2"/><path d="M2 12h20" stroke="#e2683c" stroke-width="2"/></svg>
        www.HollowThicket.example
      </li>
    </ul>
    <div class="mascot-area" role="img" aria-label="Photograph of a roaring grizzly bear"></div>
  </section>

  <section class="card card--back">
    <div class="game-name">Hollow<br>Thicket</div>
  </section>
</main>
</body>
</html>
```